Federal Government Proposal Development Consulting company needs a website designed and coded

I am looking for someone to design (using an existing logo, color palette, and text fonts) and code a wordpress-based website for a Proposal Development consulting company. I have full copy for all site pages and suggestions for images/ graphics and a few example design templates to go from.

One note, from a color perspective - I included a mockup of a business card to highlight a color scheme that I tend to like - if you look at the back of the business card, the blend of the grey, blue, with the neon green highlight as a separator really seems to pop. Just a thought as you are designing the page.

I would like to see 2-3 potential design layouts, and I will select one to move forward with. Then, I would like the site to be coded for WordPress (I can provide a login to my wordpress site). I would like 1 opportunity to review the coded site and make any final tweaks.

```html
<!DOCTYPE html>
<html lang="en">
<head>
<meta charset="utf-8">
<title>The Quill Draft Consulting LLC</title>
<link href="https://fonts.googleapis.com/css2?family=Kurale&family=Questrial&display=swap" rel="stylesheet">
<style>
:root{
  --navy:#17175f;
  --navy-deep:#0e0e45;
  --teal:#1ee8b4;
  --teal-dark:#12c99a;
  --grey:#5a5e66;
  --grey-dark:#4b4e56;
  --text:#3e3e46;
  --light:#f2f2f3;
  --white:#ffffff;
}
*{margin:0;padding:0;box-sizing:border-box}
html,body{width:1200px;height:5093px;overflow:hidden}
body{position:relative;font-family:"Questrial",sans-serif;color:var(--text);background:var(--white)}
.abs{position:absolute}
.heading{font-family:"Kurale",serif;font-weight:400;color:var(--navy);text-align:center}
.btn{position:absolute;background:var(--teal);color:var(--navy);font-size:15px;letter-spacing:.5px;display:flex;align-items:center;justify-content:center;text-transform:uppercase}

/* header */
.brand{left:110px;top:26px;font-family:"Questrial",sans-serif;color:var(--grey);font-size:30px;display:flex;align-items:center;gap:12px}
.brand small{display:block;font-size:13px;color:var(--grey)}
.brand-dot{width:22px;height:22px;border-radius:50%;background:var(--navy)}
.contact-top{top:36px;display:flex;align-items:center;gap:18px;font-size:15px;color:var(--text)}
.icon-sq{width:34px;height:34px;background:var(--teal-dark);display:flex;align-items:center;justify-content:center}
.navbar{left:455px;top:100px;width:745px;height:50px;background:var(--navy-deep);clip-path:polygon(30px 0,100% 0,100% 100%,0 100%)}
.navbar ul{list-style:none;display:flex;gap:37px;position:absolute;left:63px;top:17px;font-size:15px;color:var(--white)}
.navbar li:first-child{color:var(--teal)}

/* hero */
.hero{left:0;top:125px;width:1200px;height:720px;background:linear-gradient(100deg,#0f1c3c 0%,#27416a 40%,#7b8aa0 70%,#3c5077 100%)}
.hero-title{left:110px;top:312px;font-family:"Kurale",serif;font-size:52px;color:var(--white)}
.hero-sub{left:110px;top:384px;font-size:26px;line-height:37px;color:var(--white)}
.dots{left:1134px;top:376px;display:flex;flex-direction:column;gap:18px;align-items:center}
.dots span{width:9px;height:9px;border-radius:50%;background:var(--white)}
.dots span.on{width:18px;height:18px;border:2px solid var(--white);background:transparent;position:relative}
.dots span.on::after{content:"";position:absolute;left:3px;top:3px;width:8px;height:8px;border-radius:50%;background:var(--white)}

/* what we do */
.intro{left:128px;width:944px;font-size:16px;line-height:26.5px;text-align:center}
.card{position:absolute;top:1305px;width:303px;height:442px;background:var(--white);box-shadow:0 4px 18px rgba(0,0,0,.12);padding:70px 20px 0 20px}
.card.dark{border-bottom:4px solid var(--navy-deep)}
.card.green{border-bottom:4px solid var(--teal)}
.card-icon{position:absolute;left:18px;top:-42px;width:86px;height:86px;border-radius:50%;display:flex;align-items:center;justify-content:center}
.card h3{font-weight:400;font-size:19px;color:var(--navy-deep);margin-bottom:12px}
.card li{list-style:none;position:relative;padding-left:26px;font-size:11.4px;line-height:20.5px;margin-bottom:10px}
.card li::before{content:"";position:absolute;left:2px;top:4px;width:10px;height:10px;border-radius:50%;background:var(--teal)}

/* who */
.who{left:0;top:1868px;width:1200px;height:534px;background:var(--light)}
.who-text{left:662px;width:426px;font-size:15px;line-height:25px;text-align:justify}

/* services */
.services{left:0;top:2402px;width:1200px;height:860px;background:radial-gradient(ellipse at 50% 40%,#23237a 0%,var(--navy) 55%,var(--navy-deep) 100%)}
.tile{position:absolute;width:303px;height:222px;border:3px solid #c8cbd6;display:flex;align-items:flex-end;justify-content:center;padding-bottom:26px;color:var(--white);font-size:17px;text-align:center;line-height:24px}
.tile.sel{border-color:var(--teal)}

/* expertise */
.sme{position:absolute;top:3473px;width:226px;height:237px;background:var(--white);box-shadow:0 4px 16px rgba(0,0,0,.12);border-bottom:4px solid var(--teal);text-align:center;font-size:17px;line-height:26px;color:var(--navy-deep);padding-top:128px}
.sme-icon{position:absolute;left:70px;top:40px;width:86px;height:86px;border-radius:50%;background:var(--grey);display:flex;align-items:center;justify-content:center}
.arrow{position:absolute;width:34px;height:34px;border-radius:50%;background:#e6e6ea;display:flex;align-items:center;justify-content:center}

/* contact */
.contact{left:0;top:3825px;width:1200px;height:425px;background:var(--light)}
.field{position:absolute;background:var(--white);border:1px solid #dedee2;font-size:15px;color:#7a7a82;padding:14px 16px}

/* testimonials */
.testi{left:0;top:4250px;width:1200px;height:560px;background:linear-gradient(180deg,#1de9b6 0%,#17d6a6 60%,#1ee8b4 100%)}
.quote{position:absolute;top:4397px;width:303px;height:263px;background:var(--white);padding:26px 22px;font-size:14.5px;line-height:25px}
.stars{color:#f1832f;font-size:14px;letter-spacing:1px;margin-bottom:4px}
.who-row{position:absolute;left:22px;bottom:26px;display:flex;align-items:center;gap:14px;font-size:14px;line-height:20px;color:var(--navy-deep)}
.avatar{width:52px;height:52px;border-radius:50%;background:#d9c7b6}

/* footer */
.footer{left:0;top:4745px;width:1200px;height:348px;background:var(--grey-dark);clip-path:polygon(0 120px,30% 70px,60% 0,100% 120px,100% 100%,0 100%)}
.footer-nav{left:0;top:4956px;width:1200px;display:flex;justify-content:center;gap:22px;color:var(--white);font-size:15px}
</style>
</head>
<body>

<!-- header -->
<div class="abs brand"><div>The Quill Draft<small>Consulting LLC</small></div><span class="brand-dot"></span></div>
<div class="abs contact-top" style="left:650px">
  <span class="icon-sq"><svg width="16" height="16" viewBox="0 0 24 24"><path fill="#17175f" d="M6.6 10.8a15 15 0 0 0 6.6 6.6l2.2-2.2c.3-.3.7-.4 1-.2 1.1.4 2.3.6 3.6.6.6 0 1 .4 1 1V20c0 .6-.4 1-1 1A17 17 0 0 1 3 4c0-.6.4-1 1-1h3.5c.6 0 1 .4 1 1 0 1.3.2 2.5.6 3.6.1.3 0 .7-.2 1z"/></svg></span>
  <span>(555) 014-2280</span>
  <span class="icon-sq" style="margin-left:22px"><svg width="16" height="14" viewBox="0 0 24 20"><path fill="#17175f" d="M0 2l12 8 12-8V0H0zM0 5v15h24V5l-12 8z"/></svg></span>
  <span>info@QuillDraftCo.com</span>
</div>

<!-- hero -->
<div class="abs hero" role="img" aria-label="Photo of two colleagues reviewing a tablet in a modern office with city lights"></div>
<svg class="abs" style="left:0;top:640px" width="1200" height="210" viewBox="0 0 1200 210" aria-hidden="true">
  <path d="M0 96 C 300 140 600 150 880 185 C 1000 160 1120 90 1200 30 L1200 210 L0 210 Z" fill="#1ee8b4" opacity=".45"/>
  <path d="M0 100 C 320 150 620 170 900 198 C 1020 168 1130 110 1200 70 L1200 210 L0 210 Z" fill="#1ee8b4"/>
  <path d="M0 100 C 330 160 650 190 900 210 L0 210 Z" fill="#ffffff"/>
  <path d="M900 210 C 1030 180 1130 135 1200 110 L1200 210 Z" fill="#ffffff"/>
</svg>
<nav class="abs navbar"><ul><li>HOME</li><li>WORK WITH US</li><li>WORK FOR US</li><li>ABOUT US</li><li>CONTACT</li></ul></nav>
<div class="abs hero-title">Generate Success</div>
<div class="abs hero-sub">Fuel Innovation in Proposal Excellence<br>with The Quill Draft!</div>
<div class="btn" style="left:110px;top:483px;width:232px;height:46px">Explore Our Services</div>
<div class="abs dots"><span></span><span class="on"></span><span></span><span></span></div>

<!-- what we do -->
<h2 class="abs heading" style="left:0;top:885px;width:1200px;font-size:50px">What We Do</h2>
<p class="abs intro" style="top:973px">The Quill Draft, specializes in advancing an organization through a comprehensive suite of services designed to modernize the proposal development process. From innovative Capture Management strategies that pinpoint lucrative opportunities, meticulous Proposal Development services that transform concepts into effective narratives, and cutting-edge Generative AI techniques that create domain-aware content accelerating proposal draft development, we are your dedicated partner in securing success. With a unique fusion of technical expertise and exceptional writing capabilities, we surpass industry standards and set new benchmarks for excellence.</p>
<p class="abs intro" style="top:1146px">Discover a dynamic approach to proposal consulting that goes beyond conventional boundaries—choose The Quill Draft for solutions that Enhance the quality of your work, Elevate your corporate advantage, and Expand your industry presence.</p>

<div class="card dark" style="left:112px">
  <div class="card-icon" style="background:var(--grey)"><svg width="40" height="40" viewBox="0 0 40 40" fill="none" stroke="#fff" stroke-width="3"><circle cx="20" cy="20" r="8"/><circle cx="20" cy="20" r="15"/><path d="M20 2v6M20 32v6M2 20h6M32 20h6"/></svg></div>
  <h3>Capture Management</h3>
  <ul><li>Elevate your business development strategy with our Capture Management services. From opportunity identification to strategic planning, our experts will guide you through a meticulous process, ensuring the pursuit of the right contracts to position your organization for success.</li>
  <li>Trust us to analyze the market, mitigate risks, and develop strategies that maximize the ability to secure lucrative opportunities.</li></ul>
</div>
<div class="card green" style="left:448px">
  <div class="card-icon" style="background:var(--teal)"><svg width="40" height="40" viewBox="0 0 40 40" fill="none" stroke="#fff" stroke-width="3"><rect x="8" y="5" width="22" height="30" rx="2"/><path d="M13 13h12M13 19h12M13 25h7M26 30l8-12"/></svg></div>
  <h3>Proposal Development</h3>
  <ul><li>Transform your vision into winning proposals with our Proposal Development services. We specialize in persuasive narratives, clear technical solutions, and strategic pricing models. From meticulous compliance reviews to captivating executive summaries, we ensure every aspect of a proposal is polished and aligned with your objectives.</li>
  <li>Turn your ideas into persuasive documents that leave a lasting impression on clients to set you apart from the competition.</li></ul>
</div>
<div class="card dark" style="left:785px">
  <div class="card-icon" style="background:var(--grey)"><svg width="40" height="40" viewBox="0 0 40 40" fill="none" stroke="#fff" stroke-width="3"><circle cx="20" cy="18" r="10"/><path d="M16 30h8M17 35h6M20 2v3M6 8l2 2M34 8l-2 2"/></svg></div>
  <h3>Generative AI</h3>
  <ul><li>Revolutionize your proposal writing process with our domain-aware Generative AI services. Using customer-installed tools, we leverage domain-aware artificial intelligence to generate innovative and tailored proposal content. This not only accelerates the proposal development timeline but also ensures content that is both dynamic and targeted.</li>
  <li>Stay ahead of the curve with proposals that not only meet industry standards but exceed expectations, thanks to the creative insights generated by our AI-driven approach.</li></ul>
</div>

<!-- who we are -->
<div class="abs who"></div>
<div class="abs" style="left:112px;top:1944px;width:488px;height:384px;background:linear-gradient(135deg,#2f4f7a,#5f88b4 55%,#a9c2cf)" role="img" aria-label="Photo of a hand writing at a desk with glowing AI and learning icons floating above"></div>
<h2 class="abs heading" style="left:662px;top:1955px;font-size:40px;text-align:left">Who We Are</h2>
<p class="abs who-text" style="top:2024px">Lorem ipsum dolor sit amet, consectetur adipiscing elit, sed do eiusmod tempor incididunt ut labore et dolore magna aliqua. Ut enim ad minim veniam, quis nostrud exercitation ullamco laboris nisi ut aliquip ex ea commo consequat duis aute irure dolorea.</p>
<p class="abs who-text" style="top:2158px">Lorem ipsum dolor sit amet, consectetur adipiscing elit, sed do eiusmod tempor incididunt ut labore et dolore magna aliqua ut enim adea.</p>
<div class="btn" style="left:662px;top:2264px;width:146px;height:46px">Learn More</div>

<!-- services -->
<div class="abs services"></div>
<h2 class="abs heading" style="left:0;top:2480px;width:1200px;font-size:48px;color:#fff">Our Services</h2>
<div class="tile" style="left:112px;top:2582px;background:linear-gradient(160deg,#243a5c,#4a6a8e)" role="img" aria-label="Photo of a hand touching an AI interface">GENERATIVE AI</div>
<div class="tile sel" style="left:448px;top:2582px;background:linear-gradient(160deg,#1c3f7a,#2e6bb0)" role="img" aria-label="Photo of two engineers working at screens">TECHNICAL<br>SOLUTIONING</div>
<div class="tile" style="left:785px;top:2582px;background:linear-gradient(160deg,#2a2f3a,#5a6170)" role="img" aria-label="Photo of a glowing lightbulb with business icons">CAPTURE<br>MANAGEMENT</div>
<div class="tile" style="left:112px;top:2840px;background:linear-gradient(160deg,#5a3b2b,#a37755)" role="img" aria-label="Photo of a team collaborating at a laptop">PROPOSAL<br>MANAGEMENT</div>
<div class="tile" style="left:448px;top:2840px;background:linear-gradient(160deg,#1a2a40,#3f5570)" role="img" aria-label="Photo of a compliance checklist interface">COMPLIANCE REVIEWS</div>
<div class="tile" style="left:785px;top:2840px;background:linear-gradient(160deg,#5f6e7c,#c3ccd3)" role="img" aria-label="Photo of a presenter briefing executives in a meeting room">EXECUTIVE SUMMARIES</div>
<div class="btn" style="left:507px;top:3124px;width:186px;height:46px">View All Services</div>

<!-- subject matter expertise -->
<h2 class="abs heading" style="left:0;top:3365px;width:1200px;font-size:50px">Subject Matter Expertise</h2>
<div class="arrow" style="left:42px;top:3574px"><svg width="10" height="12" viewBox="0 0 10 12"><path d="M8 1 2 6l6 5" stroke="#17175f" stroke-width="2" fill="none"/></svg></div>
<div class="arrow" style="left:1124px;top:3574px"><svg width="10" height="12" viewBox="0 0 10 12"><path d="M2 1l6 5-6 5" stroke="#17175f" stroke-width="2" fill="none"/></svg></div>
<div class="sme" style="left:112px"><div class="sme-icon"><svg width="40" height="40" viewBox="0 0 40 40" fill="none" stroke="#fff" stroke-width="3"><rect x="10" y="10" width="20" height="20"/><path d="M15 4v6M25 4v6M15 30v6M25 30v6M4 15h6M4 25h6M30 15h6M30 25h6"/></svg></div>Generative AI</div>
<div class="sme" style="left:362px"><div class="sme-icon"><svg width="40" height="40" viewBox="0 0 40 40" fill="none" stroke="#fff" stroke-width="3"><rect x="4" y="7" width="32" height="22" rx="2"/><path d="M14 35h12M16 14l-4 4 4 4M24 14l4 4-4 4"/></svg></div>Software/ Hardware<br>Engineering</div>
<div class="sme" style="left:612px"><div class="sme-icon"><svg width="40" height="40" viewBox="0 0 40 40" fill="none" stroke="#fff" stroke-width="3"><rect x="6" y="6" width="28" height="28" rx="2"/><path d="M12 26v-6M20 26v-12M28 26v-9"/></svg></div>Systems Engineering</div>
<div class="sme" style="left:862px"><div class="sme-icon"><svg width="40" height="40" viewBox="0 0 40 40" fill="none" stroke="#fff" stroke-width="3"><path d="M11 26a7 7 0 0 1 1-14 9 9 0 0 1 17 2 6 6 0 0 1 0 12z"/><path d="M15 30v5M20 30v5M25 30v5"/></svg></div>High-Performance<br>Computing (HPC)</div>

<!-- contact -->
<div class="abs contact"></div>
<h2 class="abs heading" style="left:0;top:3877px;width:1200px;font-size:44px">Contact Us</h2>
<div class="field" style="left:165px;top:3963px;width:283px;height:47px">Name</div>
<div class="field" style="left:456px;top:3963px;width:284px;height:47px">Phone</div>
<div class="field" style="left:750px;top:3963px;width:284px;height:47px">Email</div>
<div class="field" style="left:165px;top:4025px;width:869px;height:92px">Message</div>
<div class="btn" style="left:514px;top:4138px;width:172px;height:46px">Send Message</div>

<!-- testimonials -->
<div class="abs testi"></div>
<h2 class="abs heading" style="left:0;top:4303px;width:1200px;font-size:44px">Testimonials</h2>
<div class="arrow" style="left:42px;top:4514px;background:#fff"><svg width="10" height="12" viewBox="0 0 10 12"><path d="M8 1 2 6l6 5" stroke="#17175f" stroke-width="2" fill="none"/></svg></div>
<div class="arrow" style="left:1124px;top:4514px;background:#fff"><svg width="10" height="12" viewBox="0 0 10 12"><path d="M2 1l6 5-6 5" stroke="#17175f" stroke-width="2" fill="none"/></svg></div>
<div class="quote" style="left:112px"><div class="stars">★★★★★</div>Lorem ipsum dolor sit amet, consec adipiscing elit, sed do eiusmod te incididunt ut labore et dolore mag aliqua ut enim ad minim.<div class="who-row"><span class="avatar" role="img" aria-label="Client portrait"></span><span>DANIEL REYES<br>USA</span></div></div>
<div class="quote" style="left:448px"><div class="stars">★★★★★</div>Lorem ipsum dolor sit amet, consec adipiscing elit, sed do eiusmod te incididunt ut labore et dolore mag aliqua ut enim ad minim.<div class="who-row"><span class="avatar" style="background:#c9cbcf" role="img" aria-label="Client portrait"></span><span>MAYA COLLINS<br>USA</span></div></div>
<div class="quote" style="left:785px"><div class="stars">★★★★★</div>Lorem ipsum dolor sit amet, consec adipiscing elit, sed do eiusmod te incididunt ut labore et dolore mag aliqua ut enim ad minim.<div class="who-row"><span class="avatar" style="background:#b89a82" role="img" aria-label="Client portrait"></span><span>DANIEL REYES<br>USA</span></div></div>

<!-- footer -->
<div class="abs footer"></div>
<div class="abs" style="left:0;top:4858px;width:1200px;text-align:center;color:#fff;font-size:30px;line-height:32px">The Quill Draft<br><span style="font-size:13px">Consulting LLC</span></div>
<div class="abs footer-nav"><span>HOME</span><span>|</span><span>WORK WITH US</span><span>|</span><span>WORK FOR US</span><span>|</span><span>ABOUT US</span><span>|</span><span>CONTACT</span></div>
<div class="abs" style="left:0;top:4994px;width:1200px;display:flex;justify-content:center;gap:16px;color:#fff;font-size:15px;align-items:center">
  <svg width="13" height="13" viewBox="0 0 24 24"><path fill="#1ee8b4" d="M6.6 10.8a15 15 0 0 0 6.6 6.6l2.2-2.2c.3-.3.7-.4 1-.2 1.1.4 2.3.6 3.6.6.6 0 1 .4 1 1V20c0 .6-.4 1-1 1A17 17 0 0 1 3 4c0-.6.4-1 1-1h3.5c.6 0 1 .4 1 1 0 1.3.2 2.5.6 3.6.1.3 0 .7-.2 1z"/></svg>
  <span>(555) 014-2280</span><span>|</span>
  <svg width="14" height="12" viewBox="0 0 24 20"><path fill="#1ee8b4" d="M0 2l12 8 12-8V0H0zM0 5v15h24V5l-12 8z"/></svg>
  <span>info@QuillDraftCo.com</span>
</div>
<div class="abs" style="left:0;top:5050px;width:1200px;text-align:center;color:#e6e6e6;font-size:12px">© 2023 The Quill Draft &nbsp; | &nbsp; All Rights Reserved</div>

</body>
</html>
```